Design website home page for pathology consulting company

Starting a new consulting company with anatomic pathologists focused on expert diagnosis and second opinions on difficult pathology cases. In the near future we will be incorporating next generation diagnostics for rare diseases of childhood into the business. These include discovery and testing of DNA for mutations.

The company is formed around one of the best known pathologists in the world named Marcel "Biscuit" Trowell. The name of the company is "BiscuitLab"

We had a logo design by SketchForum - it is great. I will attach file as soon as I have it (contest ending today). Our company is medical, uses microscopes, DNA, probably will focus on childhood diseases but not solely on childhood diseases. we're not particularly conservative, but the customers we want to appeal to include older practicing pathologists as well as patients (sometimes parents) looking for second opinions.

Think a group of expert doctors diagnosing disease through the microscope and through DNA technology, ages ranging from 35-75 all trained by the best pathologist in the world - "Biscuit"

We receive glass slides from diseases from patients all over the world from docs who need an expert to tell them what is the diagnosis. So "path to the diagnosis" is also part of the company marketing message.

We want the website design to describe our company but be very simple to find what one is looking for as we will use it as the launch page to:
1) order services
2) check results/reports
3) set up new account
4) speak with one of the pathologists
5) see our test menu
6) access our educational material/webinars
Updates

Update - looking for home page design and then finalists will ask for second page design to keep with theme - ok?

Reason: realized this project isn't web design but web home page design - thanks

Reason: Holidays for some in next two weeks

Reason: Hot discussion among collaborators for a few of the submissions. Will provide detail individually this weekend. Thanks so much for all the submissions!

Target Market(s)

Referring pathologists, physicians who want second opinions on pathology disease diagnosis, patients who have had biopsies (either patients themselves or parents of patients), generally high education level

Industry/Entity Type

Marketing

Requirements
Must have
• BiscuitLab
Next Generation Pathology Consultants

```html
<!DOCTYPE html>
<html lang="en">
<head>
<meta charset="utf-8">
<title>BiscuitLab – Next Generation Pathology Consultants</title>
<link href="https://fonts.googleapis.com/css2?family=Open+Sans:wght@300;400;600;700&display=swap" rel="stylesheet">
<style>
:root{
  --blue:#2377c9;
  --navy:#0c4b9c;
  --deep:#0d3f83;
  --foot:#2a6cb3;
  --foot-dark:#0f4a8e;
  --ink:#6b6b6b;
  --link:#1a5fae;
  --band:#ececec;
  --ring:#c9ccd1;
}
*{margin:0;padding:0;box-sizing:border-box}
html,body{width:862px;height:1200px;overflow:hidden;background:#fff;font-family:'Open Sans',Arial,sans-serif}
.page{position:relative;width:862px;height:1200px;overflow:hidden}
.abs{position:absolute}
/* header */
.header{left:78px;top:0;width:685px;height:88px;background:linear-gradient(160deg,#fff 40%,#eef1f5 70%,#fff 100%)}
.brand{left:86px;top:8px;display:flex;flex-direction:column;align-items:center}
.brand-dot{width:50px;height:50px;border-radius:50%;background:#8d96a3;margin-bottom:3px}
.brand-name{font-size:19px;font-weight:600;color:var(--navy);letter-spacing:.5px;line-height:1}
.brand-tag{font-size:6px;color:#556;margin-top:2px}
.toplinks{top:28px;display:flex}
.toplink{font-size:11.5px;color:var(--link);padding:0 10px;border-left:1px solid #c6d3e3}
.toplink:first-child{border-left:none}
.toplink small{display:block;font-size:8.5px;line-height:11px;margin-top:3px}
/* nav */
.nav{left:78px;top:88px;width:685px;height:31px;background:var(--blue);display:flex;align-items:center}
.nav a{color:#fff;font-size:11px;text-decoration:none;padding:0 12.5px;height:31px;line-height:31px}
.nav a.active{background:#fff;color:var(--blue)}
.search{position:absolute;right:6px;top:5px;width:134px;height:20px;background:#fff;border:1px solid #b9c9dc;font-size:9px;color:#999;padding:3px 5px}
/* hero */
.hero{left:78px;top:119px;width:685px;height:353px;background:linear-gradient(120deg,#e9edf1 0%,#d8dde2 45%,#b9c0c7 70%,#e7eaee 100%)}
.hero-tubes{left:78px;top:400px;width:400px;height:72px;background:linear-gradient(180deg,#8fcfe8,#3aa7d6)}
.hero-title{left:91px;top:296px;font-size:36px;font-weight:300;color:var(--navy);letter-spacing:.5px}
.hero-sub{left:92px;top:343px;font-size:17px;font-weight:300;color:var(--navy)}
.btn-learn{left:94px;top:369px;width:89px;height:24px;background:var(--navy);color:#fff;font-size:11px;text-align:center;line-height:24px;border-radius:2px}
/* speak bar */
.speak{left:78px;top:472px;width:686px;height:35px;background:var(--navy)}
.speak-label{left:78px;top:472px;width:140px;height:35px;background:var(--blue);color:#fff;font-size:11.5px;line-height:35px;padding-left:9px;clip-path:polygon(0 0,93% 0,100% 50%,93% 100%,0 100%)}
.field{top:479px;height:22px;background:#fff;font-size:9.5px;color:#bbb;padding:4px 6px}
.field-ico{top:479px;width:22px;height:22px;background:var(--blue);color:#fff;font-size:10px;text-align:center;line-height:22px}
.btn-start{left:578px;top:478px;width:90px;height:24px;background:var(--blue);color:#fff;font-size:11.5px;text-align:center;line-height:24px;border-radius:2px}
/* services */
.svc{top:548px;width:190px;text-align:center}
.svc-icon{width:88px;height:88px;border-radius:50%;background:var(--navy);border:4px solid var(--ring);margin:0 auto;display:flex;align-items:center;justify-content:center}
.svc h3{font-size:13px;font-weight:600;color:var(--navy);margin-top:16px}
.svc p{font-size:8.3px;line-height:13px;color:var(--ink);margin-top:8px}
/* why us */
.why-title{left:116px;top:776px;font-size:12px;color:var(--link)}
.why{top:760px;width:150px}
.why h4{font-size:11.5px;font-weight:400;color:var(--link)}
.why p{font-size:6.8px;line-height:12.8px;color:#444;margin-top:4px}
.why-rule{top:760px;width:1px;height:57px;background:#d5d9de}
/* band */
.band{left:0;top:844px;width:862px;height:146px;background:var(--band);box-shadow:inset 0 3px 3px -2px #cfcfcf}
.micro-img{left:108px;top:862px;width:152px;height:110px;background:linear-gradient(135deg,#1a3aa0,#4a6ec5 45%,#c9cdd2 70%,#6e7b8b);border:3px solid #fff}
.diag h3{font-size:11.5px;font-weight:600;color:var(--navy)}
.diag p{font-size:8.2px;line-height:12.8px;color:#444;margin-top:3px}
.btn-check{left:269px;top:952px;width:88px;height:15px;background:var(--navy);color:#fff;font-size:6.8px;font-weight:700;text-align:center;line-height:15px}
.card{left:523px;top:864px;width:193px;height:105px;background:#fff}
.card h3{font-size:10px;font-weight:700;color:var(--navy);position:absolute;left:12px;top:12px}
.card-img{left:12px;top:28px;width:69px;height:67px;background:linear-gradient(160deg,#dfe6ee,#fff 50%,#a8b4c2)}
.card p{left:89px;top:34px;width:95px;font-size:6.8px;line-height:12.8px;color:#444}
.btn-call{left:91px;top:76px;width:81px;height:15px;background:var(--navy);color:#fff;font-size:8.5px;text-align:center;line-height:15px}
/* footer */
.footer{left:0;top:990px;width:862px;height:176px;background:var(--foot);color:#fff}
.foot-h{font-size:10px;font-weight:700;color:#fff}
.foot-p{font-size:8.2px;line-height:13.6px;color:#fff}
.foot-menu li{list-style:none;font-size:8px;margin-bottom:15px;padding-left:7px;position:relative}
.foot-menu li::before{content:"";position:absolute;left:0;top:2px;border-left:3px solid #9cc3ec;border-top:2.5px solid transparent;border-bottom:2.5px solid transparent}
.btn-more{left:114px;top:1116px;width:85px;height:16px;background:#4aa3d8;color:#0b2f62;font-size:8.5px;text-align:center;line-height:16px}
.social{top:1027px;width:24px;height:24px;background:#2e3f59;border-radius:2px}
.email{left:421px;top:1085px;width:125px;height:17px;background:var(--deep);font-size:8.3px;font-weight:700;padding:2px 7px;line-height:13px}
.btn-enter{left:489px;top:1112px;width:56px;height:16px;background:#4aa3d8;color:#0b2f62;font-size:8.5px;text-align:center;line-height:16px}
.loc{font-size:8px;line-height:10px;font-weight:600;padding-left:11px;position:relative}
.loc svg{position:absolute;left:0;top:1px}
.wait-small{left:581px;top:1109px;font-size:10px}
.wait-big{left:579px;top:1118px;font-size:17px}
.wait-badge{left:665px;top:1101px;width:51px;height:51px;border-radius:50%;background:radial-gradient(circle at 40% 35%,#e4e4e4,#a9a9a9);color:#444;font-size:15px;font-style:italic;text-align:center;line-height:14px;padding-top:10px}
.bottom{left:0;top:1166px;width:862px;height:34px;background:var(--foot-dark);color:#fff;font-size:7.5px;font-weight:700}
</style>
</head>
<body>
<div class="page">

  <header>
    <div class="abs header"></div>
    <div class="abs brand">
      <div class="brand-dot"></div>
      <div class="brand-name">BiscuitLab</div>
      <div class="brand-tag">Next Generation Pathology Consultants</div>
    </div>
    <div class="abs toplinks" style="left:457px">
      <div class="toplink">Welcome (login)<small>Your Account</small></div>
      <div class="toplink">See Test Menu<small>Lorem ipsum dolor sit<br>amet, consectetur</small></div>
      <div class="toplink">Order Services<small>Lorem ipsum dolor sit<br>consectetur adipiscing</small></div>
    </div>
    <nav class="abs nav">
      <a class="active">HOME</a><a>ABOUT</a><a>OUR PRACTICE</a><a>NEWS/EVENTS</a><a>BLOG</a><a>APPOINTMENT</a><a>CONTACT</a>
      <div class="search">Search..
        <svg width="13" height="13" viewBox="0 0 13 13" style="position:absolute;right:4px;top:3px"><circle cx="5.5" cy="5.5" r="4.3" fill="none" stroke="#888" stroke-width="1.2"/><line x1="8.6" y1="8.6" x2="12" y2="12" stroke="#888" stroke-width="1.4"/></svg>
      </div>
    </nav>
  </header>

  <section>
    <div class="abs hero" role="img" aria-label="Photo of two pathologists in lab coats examining samples at a microscope"></div>
    <div class="abs hero-tubes" role="img" aria-label="Rack of blue test tubes"></div>
    <h1 class="abs hero-title">BISCUIT LAB</h1>
    <p class="abs hero-sub">Next Generation Pathology Consultants</p>
    <div class="abs btn-learn">Learn more</div>
  </section>

  <section>
    <div class="abs speak"></div>
    <div class="abs speak-label">Speak With &nbsp;Patho logist</div>
    <div class="abs field" style="left:244px;width:110px">name</div>
    <div class="abs field-ico" style="left:354px">
      <svg width="10" height="10" viewBox="0 0 10 10" style="margin-top:6px"><circle cx="5" cy="3" r="2.4" fill="#fff"/><path d="M0.5 10c0-3 2-4.5 4.5-4.5S9.5 7 9.5 10z" fill="#fff"/></svg>
    </div>
    <div class="abs field" style="left:382px;width:70px">email</div>
    <div class="abs field-ico" style="left:452px">@</div>
    <div class="abs field" style="left:480px;width:65px">date</div>
    <div class="abs field-ico" style="left:545px">
      <svg width="10" height="10" viewBox="0 0 10 10" style="margin-top:6px"><rect x="1" y="2" width="8" height="7" fill="none" stroke="#fff" stroke-width="1.3"/><rect x="1" y="2" width="8" height="2" fill="#fff"/></svg>
    </div>
    <div class="abs btn-start">Start Now</div>
  </section>

  <section>
    <div class="abs svc" style="left:92px">
      <div class="svc-icon">
        <svg width="40" height="44" viewBox="0 0 40 44"><circle cx="20" cy="9" r="6" fill="#fff"/><circle cx="20" cy="29" r="12" fill="#fff"/><circle cx="22" cy="28" r="5" fill="#0c4b9c"/></svg>
      </div>
      <h3>Childhood Diseases</h3>
      <p>Lorem ipsum dolor sit amet, consectetur adipiscing elit. Niihunclorem est, eleifend elefend in nunc.</p>
    </div>
    <div class="abs svc" style="left:320px">
      <div class="svc-icon">
        <svg width="38" height="36" viewBox="0 0 38 36"><circle cx="19" cy="10" r="8" fill="#fff"/><path d="M3 36c0-10 7-15 16-15s16 5 16 15z" fill="#fff"/></svg>
      </div>
      <h3>Second opinion</h3>
      <p>Lorem ipsum dolor sit amet, consectetur adipiscing elit. Niihunclorem est, eleifend elefend in nunc.</p>
    </div>
    <div class="abs svc" style="left:543px">
      <div class="svc-icon">
        <svg width="24" height="48" viewBox="0 0 24 48"><path d="M4 2C4 14 20 14 20 24S4 34 4 46M20 2C20 14 4 14 4 24s16 10 16 22" fill="none" stroke="#fff" stroke-width="3"/><g stroke="#fff" stroke-width="2"><line x1="7" y1="7" x2="17" y2="7"/><line x1="7" y1="17" x2="17" y2="17"/><line x1="7" y1="31" x2="17" y2="31"/><line x1="7" y1="41" x2="17" y2="41"/></g></svg>
      </div>
      <h3>DNA Technology</h3>
      <p>Lorem ipsum dolor sit amet, consectetur adipiscing elit. Niihunclorem est, eleifend elefend in nunc.</p>
    </div>
  </section>

  <section>
    <h2 class="abs why-title" style="font-weight:400">What Sets up Apart</h2>
    <div class="abs why" style="left:264px"><h4>Technology</h4><p>Lorem ipsum dolor sit amet,<br>adipiscing elit. Niihunclorem<br>elefend in nunc.</p></div>
    <div class="abs why-rule" style="left:385px"></div>
    <div class="abs why" style="left:425px"><h4>Quality of Care</h4><p>Lorem ipsum dolor sit amet,<br>adipiscing elit. Niihunclorem<br>elefend in nunc.</p></div>
    <div class="abs why-rule" style="left:548px"></div>
    <div class="abs why" style="left:590px"><h4>Patience Experience</h4><p>Lorem ipsum dolor sit amet,<br>adipiscing elit. Niihunclorem<br>elefend in nunc.</p></div>
  </section>

  <section>
    <div class="abs band"></div>
    <div class="abs micro-img" role="img" aria-label="Photo of a pathologist working at a laboratory microscope"></div>
    <div class="abs diag" style="left:269px;top:861px;width:245px">
      <h3>Dignosis Of Diseases By Using Microscopes</h3>
      <p>Lorem ipsum dolor sit amet, consecteturelit. Niihunclorem est, eleifend velcursrtus aelefend in nunc. Nulla agcigisi.moirbi sce ierisque serm vitea massa feugiatut varipusmhurisorganarie. sed prelium felts eget adminut varipus mhurisorganarie. sed prelium get of nullum.</p>
    </div>
    <div class="abs btn-check">CHECK RESULT/REPORTS</div>
    <div class="abs card">
      <h3>Speak With One Of The pathologist</h3>
      <div class="abs card-img" role="img" aria-label="Photo of a pathologist beside a microscope"></div>
      <p class="abs">Lorem ipsum dolor sit amet, adipiscing elit. Niihunclorem elefend in nunc.</p>
      <div class="abs btn-call">CALL NOW</div>
    </div>
  </section>

  <footer>
    <div class="abs footer"></div>
    <div class="abs" style="left:114px;top:1003px;width:160px">
      <div class="foot-h">Educational Materials</div>
      <p class="foot-p" style="margin-top:9px">Lorem ipsum dolor sit amet, adipiscin. Niihunclorem &nbsp;elefend in nunc.<br>Lorem ipsum dolor sit amet, adipiscin. Niihunclorem &nbsp;elefend in nunc.<br>Lorem ipsum dolor sit amet, adipiscin. Niihunclorem &nbsp;elefend in nunc.</p>
    </div>
    <div class="abs btn-more">MORE DETAIL</div>
    <div class="abs" style="left:300px;top:1003px;color:#fff">
      <div class="foot-h">Test Menu</div>
      <ul class="foot-menu" style="margin-top:10px"><li>HOME</li><li>PHYSICIANS</li><li>SPECIALITIES</li><li>INFO</li></ul>
    </div>
    <div class="abs foot-h" style="left:421px;top:1003px">Contact</div>
    <div class="abs social" style="left:421px"></div>
    <div class="abs social" style="left:451px"></div>
    <div class="abs social" style="left:481px"></div>
    <div class="abs social" style="left:511px"></div>
    <div class="abs foot-h" style="left:421px;top:1065px">New account</div>
    <div class="abs email">Enter your Email :</div>
    <div class="abs btn-enter">Enter</div>
    <div class="abs" style="left:572px;top:1003px;color:#fff">
      <div class="foot-h">Locations</div>
      <div class="loc" style="margin-top:10px">
        <svg width="7" height="9" viewBox="0 0 7 9"><path d="M3.5 0A3.2 3.2 0 0 0 .3 3.2C.3 5.5 3.5 9 3.5 9s3.2-3.5 3.2-5.8A3.2 3.2 0 0 0 3.5 0z" fill="#fff"/><circle cx="3.5" cy="3.2" r="1.2" fill="#2a6cb3"/></svg>
        elm row ,name .city ,country<br>zip code : 204816</div>
      <div class="loc" style="margin-top:13px">
        <svg width="7" height="9" viewBox="0 0 7 9"><path d="M3.5 0A3.2 3.2 0 0 0 .3 3.2C.3 5.5 3.5 9 3.5 9s3.2-3.5 3.2-5.8A3.2 3.2 0 0 0 3.5 0z" fill="#fff"/><circle cx="3.5" cy="3.2" r="1.2" fill="#2a6cb3"/></svg>
        elm row ,name .city ,country<br>zip code : 204816</div>
    </div>
    <div class="abs wait-small" style="color:#fff">Average</div>
    <div class="abs wait-big" style="color:#fff">wait time</div>
    <div class="abs wait-badge">10<br>min</div>
    <div class="abs bottom">
      <span class="abs" style="left:113px;top:12px">COPYRIGHT © 2013. BISCUIT LAB ALL RIGHTS RESERVED.</span>
      <span class="abs" style="left:600px;top:12px">SITEMAP &nbsp;&nbsp; | &nbsp;&nbsp; PRIVACY POLICY</span>
    </div>
  </footer>

</div>
</body>
</html>
```